Exciting & Elegant Stationary Pack

Stationary consists of
1. Letter head / Envelope
2. Business Card
3. Invoice
4. 40x40mm sticker

Attached files;

1. Logo (Other formats available on request)
2. MS word Doc - For information and description of design
3. Website image (This will be our new website so use the colours so everything ties together)
4. Sample of stationary pack we like, but feel free to be creative

Target Market(s)

Home improvement

Industry/Entity Type

Construction

Font styles to use
Other font styles liked:
• Leave up to designer - We like font used on (website attached image)

Requirements
Must have
• Please look at uploaded file of sample website and use colours
Nice to have
• Any type of business card design - eg. metal, die cut, embossed, etc...

```html
<!DOCTYPE html>
<html lang="en">
<head>
<meta charset="utf-8">
<title>Setter &amp; Grout — Business Card</title>
<link href="https://fonts.googleapis.com/css2?family=Open+Sans:wght@400;600;700&display=swap" rel="stylesheet">
<style>
  :root {
    --backdrop: #8b8c8d;
    --card: #f4f4f2;
    --navy: #1f3a63;
    --orange: #c98a44;
    --ink: #3a3d42;
    --muted: #6b6f75;
  }
  * { box-sizing: border-box; margin: 0; padding: 0; }
  html, body { width: 1200px; height: 814px; overflow: hidden; }
  body {
    background: var(--backdrop);
    font-family: "Open Sans", Arial, sans-serif;
    position: relative;
  }
  .card {
    position: absolute;
    top: 254px;
    width: 500px;
    height: 306px;
    background: var(--card);
    overflow: hidden;
  }
  .card--contact { left: 60px; }
  .card--brand { left: 640px; }

  /* contact side */
  .brand-lockup {
    position: absolute;
    left: 44px;
    top: 100px;
    width: 176px;
    display: flex;
    align-items: center;
    gap: 12px;
  }
  .brand-lockup__square {
    width: 22px; height: 22px;
    flex: none;
    background: var(--navy);
  }
  .brand-name {
    font-weight: 700;
    font-size: 20px;
    line-height: 24px;
    color: var(--navy);
    letter-spacing: 0.5px;
    text-transform: uppercase;
  }
  .contact {
    position: absolute;
    left: 262px;
    top: 92px;
    color: var(--ink);
  }
  .contact__name {
    font-weight: 700;
    font-size: 17px;
    color: var(--navy);
  }
  .contact__role {
    font-weight: 600;
    font-size: 12px;
    color: var(--orange);
    margin-top: 1px;
  }
  .contact__licence {
    font-size: 12px;
    color: var(--muted);
    margin-top: 8px;
  }
  .contact__list { list-style: none; margin-top: 8px; }
  .contact__list li {
    display: flex;
    align-items: center;
    gap: 8px;
    font-size: 12.5px;
    line-height: 20px;
  }
  .contact__list svg { width: 12px; height: 12px; flex: none; }

  /* brand side */
  .brand-title {
    position: absolute;
    right: 40px;
    top: 36px;
    font-weight: 700;
    font-size: 26px;
    line-height: 34px;
    color: var(--navy);
    letter-spacing: 1px;
    text-transform: uppercase;
  }
  .brand-band {
    position: absolute;
    left: 318px;
    top: 78px;
    width: 78px;
    bottom: 0;
    background: var(--navy);
  }
</style>
</head>
<body>

<section class="card card--contact" aria-label="Business card, contact side">
  <div class="brand-lockup">
    <span class="brand-lockup__square"></span>
    <span class="brand-name">Setter &amp;<br>Grout</span>
  </div>

  <div class="contact">
    <p class="contact__name">Linh Tran</p>
    <p class="contact__role">Project Manager</p>
    <p class="contact__licence">Lic No. 204518c</p>
    <ul class="contact__list">
      <li>
        <svg viewBox="0 0 12 12" aria-hidden="true"><rect x="3" y="0.8" width="6" height="10.4" rx="1" fill="none" stroke="#1f3a63" stroke-width="1.2"/><circle cx="6" cy="9.3" r="0.7" fill="#1f3a63"/></svg>
        0400 318 722
      </li>
      <li>
        <svg viewBox="0 0 12 12" aria-hidden="true"><rect x="0.5" y="2" width="11" height="8" fill="#1f3a63"/><path d="M0.8 2.4 6 6.6 11.2 2.4" fill="none" stroke="#f4f4f2" stroke-width="1"/></svg>
        hello@settergrout.com.au
      </li>
      <li>
        <svg viewBox="0 0 12 12" aria-hidden="true"><circle cx="6" cy="6" r="5.5" fill="#1f3a63"/><path d="M0.8 6h10.4M6 0.8c-2.4 2.6-2.4 7.8 0 10.4M6 0.8c2.4 2.6 2.4 7.8 0 10.4" fill="none" stroke="#f4f4f2" stroke-width="0.8"/></svg>
        www.settergrout.com.au
      </li>
    </ul>
  </div>
</section>

<section class="card card--brand" aria-label="Business card, brand side">
  <p class="brand-title">Setter &amp; Grout</p>
  <div class="brand-band"></div>
</section>

</body>
</html>
```